Harwick Moss Fine Art gallery website - Modern british art for sale

We need a website design that is both current and high end. Our products are expensive and this should be reflected in the look of the website. We would like the logo we had designed last year to be clearly seen in the design. We want sleek, simple, and easy to navigate. Nothing too colourful as the colours of the art should always take precedence.

Target Market(s)

The average price of one our products starts at £250 and can go up to £10,000 we are an entry level gallery.

Industry/Entity Type

Art Gallery

Number of Pages Required

5+ page

Font styles to use
Sans Serif

Colors
000000
ffffff
faa54b
abd037
886aae
b868aa

Requirements
Must have
• Attractive front page. Linked to our Chirper feed.
• 4 links from front page - New Releases, about us, Artists, contact us
• Social media links - Linkbook, Chirper, Reelcast, Snapframe.
• Each artist must have their own page, each page must have a biography link to another page.
Nice to have
• Utilise our new logo design. I would like the Chirper feed to link to the front page in a small way so you can see what's being said on Chirper by the company. For future proofing maybe have a locations function on the front page which can be adroit down menu showing where our other galleries are.

```html
<!DOCTYPE html>
<html lang="en">
<head>
<meta charset="utf-8">
<title>Harwick Moss Fine Art</title>
<link rel="stylesheet" href="https://fonts.googleapis.com/css2?family=Cinzel:wght@400;700&family=Lato:wght@400;700&display=swap">
<style>
:root{
  --black:#000000;
  --white:#ffffff;
  --orange:#faa54b;
  --green:#abd037;
  --violet:#886aae;
  --orchid:#b868aa;
  --charcoal:#1b1b1b;
  --mist:#f5f5f5;
  --ink:#222222;
  --link:#1a9ad6;
  --rule:#d9d9d9;
}
*{box-sizing:border-box;margin:0;padding:0}
html,body{width:750px;height:1200px;overflow:hidden;background:var(--white)}
body{position:relative;font-family:'Lato',sans-serif;color:var(--ink)}
.abs{position:absolute}

/* header */
.site-header{left:0;top:0;width:750px;height:86px;
  background:radial-gradient(ellipse at 50% 30%,#3a3a3a 0%,#1e1e1e 55%,#121212 100%);}
.brand{left:0;top:46px;width:750px;text-align:center;font-family:'Cinzel',serif;
  font-size:22px;color:#e6e1d6;letter-spacing:1px}
.brand-dot{left:369px;top:20px;width:12px;height:12px;border-radius:50%;background:#c9a24a}
.main-nav{left:0;top:86px;width:750px;height:28px;background:var(--black);
  border-top:1px solid #333;display:flex;justify-content:center;align-items:center}
.main-nav a,.footer-nav a{font-family:'Cinzel',serif;color:var(--white);text-decoration:none;
  font-size:10.5px;letter-spacing:.5px;padding:0 18px;border-left:1px solid #444}
.main-nav a:first-child,.footer-nav a:first-child{border-left:none}

/* feature */
.feature-art{left:57px;top:138px;width:316px;height:368px;
  background:linear-gradient(160deg,#f4f1ea 0%,#e8e3d9 45%,#d8d2c6 70%,#f0ece4 100%)}
.feature-panel{left:373px;top:138px;width:319px;height:368px;background:var(--orchid)}
.feature-title{left:400px;top:322px;font-family:'Cinzel',serif;font-size:19px;color:var(--white);letter-spacing:.5px}
.feature-text{left:400px;top:354px;width:274px;font-size:8.4px;line-height:12.3px;color:#f8eef6}
.feature-rule{left:400px;top:421px;width:272px;height:1px;background:rgba(255,255,255,.35)}
.thumb{top:435px;width:65px;height:60px;border:1px solid var(--white)}
.thumb.active{border:2px solid var(--black)}
.pager{left:361px;top:454px;width:13px;height:23px;background:var(--orchid)}

/* gallery strip */
.gallery{left:0;top:528px;width:750px;height:262px;background:var(--mist)}
.card{top:554px;width:317px;height:203px}
.card-caption{left:0;bottom:0;width:100%;height:54px;background:rgba(255,255,255,.78);text-align:center}
.card-title{font-family:'Cinzel',serif;font-size:17px;font-weight:700;color:var(--ink);margin-top:8px;letter-spacing:.5px}
.card-date{font-size:9.5px;color:var(--ink);margin-top:2px}

/* about & feeds */
.section-head{top:818px;height:28px;border-bottom:1px solid var(--rule);display:flex;align-items:center}
.head-mark{width:14px;height:14px;border:1px solid var(--ink);border-radius:50%;margin-right:10px}
.section-head h2{font-family:'Cinzel',serif;font-weight:400;font-size:17px;color:var(--ink);letter-spacing:.3px;white-space:nowrap}
.see-all{left:632px;top:829px;font-size:7.5px;color:var(--link)}
.about-text{left:58px;top:860px;width:315px;font-size:8.4px;line-height:14px;color:var(--ink);text-align:justify}
.tweet{left:400px;width:292px;height:52px}
.tweet-icon{left:0;top:2px;width:32px;height:32px;border:2px solid var(--link);border-radius:50%}
.tweet-body{left:40px;top:0;width:252px;font-size:7.6px;line-height:13.5px;color:#444}
.tweet-body .hl{color:var(--link)}
.tweet-rule{left:400px;top:910px;width:292px;height:1px;background:#e6e6e6}

/* newsletter */
.newsletter{left:0;top:980px;width:750px;height:100px;background:var(--mist)}
.news-icon{left:119px;top:1011px;width:34px;height:34px;border-radius:50%;background:var(--orange)}
.news-title{left:165px;top:1012px;font-family:'Cinzel',serif;font-size:13px;color:#333;letter-spacing:.3px}
.news-sub{left:164px;top:1031px;font-size:8px;color:#555}
.news-input{left:323px;top:1014px;width:210px;height:28px;background:var(--white);border:1px solid #cfcfcf;
  font-size:8.5px;padding:9px 8px;color:#222}
.news-button{left:533px;top:1014px;width:97px;height:28px;background:var(--orange);color:var(--white);
  font-family:'Cinzel',serif;font-size:11.5px;text-align:center;line-height:28px;letter-spacing:.5px}

/* footer */
.site-footer{left:0;top:1057px;width:750px;height:143px}
.social{top:1115px;width:19px;height:19px;background:var(--white)}
.footer-nav{left:0;top:1147px;width:750px;display:flex;justify-content:center}
.footer-nav a{color:#cfcfcf;font-size:9.5px;padding:0 17px}
.copyright{left:0;top:1168px;width:750px;text-align:center;font-size:7.8px;color:#bdbdbd}
.color-strip{left:0;top:1196px;width:750px;height:4px;display:flex}
.color-strip span{flex:1}
</style>
</head>
<body>

<header class="abs site-header"></header>
<div class="abs brand-dot"></div>
<div class="abs brand">Harwick Moss Fine Art</div>
<nav class="abs main-nav">
  <a>New Releases</a><a>About Us</a><a>Artists</a><a>Location</a>
</nav>

<div class="abs feature-art" role="img" aria-label="Print of a dark cathedral tower with an orange building in a sketched city"></div>
<div class="abs feature-panel"></div>
<div class="abs pager">
  <svg width="13" height="23" viewBox="0 0 13 23"><path d="M5 9 L2.5 11.5 L5 14 M8 9 L10.5 11.5 L8 14" fill="none" stroke="#fff" stroke-width="1.2"/></svg>
</div>
<div class="abs feature-title">Ashby Harbour</div>
<p class="abs feature-text">Lorem ipsum dolor sit amet, consectetuer adipiscing elit, sed diam sit nonummy nibh euismod tincidunt ut laoreet dolore magna aliquam erat volutpat. Ut wisi enim ad minim veniam, quis nostrud exerci tation almet ullamcorper suscipit lobortis nisl ut aliquip ex.</p>
<div class="abs feature-rule"></div>
<div class="abs thumb active" style="left:399px;background:linear-gradient(#f1eee8,#4a4a4a 70%,#e1521e)" role="img" aria-label="Thumbnail of the tower print"></div>
<div class="abs thumb" style="left:468px;background:linear-gradient(135deg,#eef0f0,#c6d3d8 55%,#e1521e)" role="img" aria-label="Thumbnail of an abstract print with red line"></div>
<div class="abs thumb" style="left:537px;background:linear-gradient(135deg,#f2f2f2,#9a9a9a 60%,#efefef)" role="img" aria-label="Thumbnail of an ink line drawing"></div>
<div class="abs thumb" style="left:607px;background:linear-gradient(135deg,#f4f4f4,#b5b5b5 60%,#f4f4f4)" role="img" aria-label="Thumbnail of dark ink figures"></div>

<section class="abs gallery"></section>
<svg class="abs" style="left:12px;top:636px" width="22" height="40" viewBox="0 0 22 40"><path d="M19 2 L3 20 L19 38" fill="none" stroke="#aaa" stroke-width="2"/></svg>
<svg class="abs" style="left:716px;top:636px" width="22" height="40" viewBox="0 0 22 40"><path d="M3 2 L19 20 L3 38" fill="none" stroke="#aaa" stroke-width="2"/></svg>

<div class="abs card" style="left:56px;background:linear-gradient(90deg,#e4eef2 0%,#2f3880 22%,#b33a4e 45%,#e8b92a 70%,#eef3f4 100%)" role="img" aria-label="Abstract print of a blue and yellow oval crossed by coloured stripes">
  <div class="abs card-caption"><div class="card-title">Wexley 2</div><div class="card-date">Lorem ipsum, 22 Feb 2017</div></div>
</div>
<div class="abs card" style="left:376px;background:linear-gradient(135deg,#f06a3c 0%,#b57ac8 30%,#d6c86a 55%,#f06a3c 80%,#c07ad0 100%)" role="img" aria-label="Abstract print of orange, violet and olive wave shapes">
  <div class="abs card-caption"><div class="card-title">Marden</div><div class="card-date">Lorem ipsum, 22 Feb 2017</div></div>
</div>

<div class="abs section-head" style="left:58px;width:315px"><span class="head-mark"></span><h2>About Harwick Moss Fine Art</h2></div>
<p class="abs about-text">Lorem ipsum dolor sit amet, consectetuer adipiscing elit, sed diam nonummy nibh euismod tincidunt ut laoreet dolore magna aliquam erat volutpat. Ut wisi enim ad minim veniam, quis nostrud exerci tation ullamcorper suscipit lobortis nisl ut aliquip ex ea commodo consequat. Duis autem vel eum iriure dolor in hendrerit in vulputate velit esse molestie consequat, vel illum dolore eu feugiat nulla facilisis at vero eros et accumsan et iusto odio dignissim qui blandit praesent luptatum zzril delenit augue duis dolore te feugait nulla facilisi.</p>

<div class="abs section-head" style="left:400px;width:292px"><span class="head-mark"></span><h2>Chirper Feeds</h2></div>
<div class="abs see-all">See All Feeds &raquo;</div>

<div class="abs tweet" style="top:862px">
  <div class="abs tweet-icon"></div>
  <div class="abs tweet-body"><span class="hl">Lorem Ipsum</span> is simply dummy text&nbsp; Tempor - Tweet tweet - Ipsum isyt<br>http://example.org/hm4821<br><span class="hl">12 minutes ago</span></div>
</div>
<div class="abs tweet-rule"></div>
<div class="abs tweet" style="top:917px">
  <div class="abs tweet-icon"></div>
  <div class="abs tweet-body"><span class="hl">Lorem Ipsum</span> is simply dummy text&nbsp; Tempor - Tweet tweet - Ipsum isyt<br>http://example.org/hm4821<br><span class="hl">12 minutes ago</span></div>
</div>

<section class="abs newsletter"></section>
<div class="abs news-icon">
  <svg width="34" height="34" viewBox="0 0 34 34"><rect x="9.5" y="12" width="15" height="10.5" rx="1.5" fill="none" stroke="#fff" stroke-width="1.4"/><path d="M9.5 13 L17 18.5 L24.5 13" fill="none" stroke="#fff" stroke-width="1.4"/></svg>
</div>
<div class="abs news-title">Join our Newsletter</div>
<div class="abs news-sub">Stay up to date with the latest news.</div>
<div class="abs news-input">Email</div>
<div class="abs news-button">Subscribe</div>

<svg class="abs site-footer" width="750" height="143" viewBox="0 0 750 143">
  <defs>
    <radialGradient id="footerTone" cx="50%" cy="45%" r="70%">
      <stop offset="0" stop-color="#2e2e2e"/><stop offset="1" stop-color="#111"/>
    </radialGradient>
  </defs>
  <path d="M0 0 L375 36 L750 0 L750 143 L0 143 Z" fill="url(#footerTone)"/>
</svg>
<div class="abs social" style="left:326px" role="img" aria-label="Linkbook page"></div>
<div class="abs social" style="left:352px" role="img" aria-label="Chirper page"></div>
<div class="abs social" style="left:378px" role="img" aria-label="Reelcast channel"></div>
<div class="abs social" style="left:404px" role="img" aria-label="Snapframe page"></div>
<nav class="abs footer-nav"><a>New Releases</a><a>About Us</a><a>Artists</a><a>Location</a></nav>
<div class="abs copyright">Copyrights &copy; 2017 Harwick Moss Fine Art. All Rights Reserve.</div>
<div class="abs color-strip"><span style="background:var(--orange)"></span><span style="background:var(--violet)"></span><span style="background:var(--green)"></span><span style="background:var(--orchid)"></span></div>

</body>
</html>
```